Lumora Systems New Website - IT Infrastructure | Smart Cabinet | Micro Data Center

We're an IT SI providing Server Room Design & Build | All-in-One Rack & Smart Cabinet | Structured Cabling | IT Relocation | Maintenance. Old website can be found at www.lumorasys.com.hk. We'd like a brand new wix website which is modern, minimalist, interactive with some animation. Website content will be mostly static and include our service, our project, news and events, about us, contacts, blogs, partners and brands, etc.

reference sites:
We'd like to see more designs referring to below

https://www.pixelvane.example/design/41736205
https://www.pixelvane.example/design/41892417
https://velbrinn.example/

Animation (scrolling effect) referring to
https://velbrinn.example/intelligence/smart-office-room/
Updates

we'd like below style.

Designs look the same

Target Market(s)

Commercials in HK

Industry/Entity Type

IT, Technology, Data Center

Coding

Coded - Design and coding required

Font styles to use
Sans Serif

Requirements
Must have
• CMS, Some Interactive Elements/ Graphics

```html
<!DOCTYPE html>
<html lang="en">
<head>
<meta charset="utf-8">
<title>Lumora Systems – IT Infrastructure</title>
<link href="https://fonts.googleapis.com/css2?family=Fira+Sans:wght@400;500;600&family=Lato:wght@400;700&display=swap" rel="stylesheet">
<style>
:root{
  --orange:#f7740f;
  --navy:#15264b;
  --navy-2:#2e3d57;
  --topbar:#1d3b4d;
  --ink:#1f2d3d;
  --text:#6b7280;
  --light:#eef2f2;
  --line:#e3e6ea;
  --white:#fff;
}
*{box-sizing:border-box;margin:0;padding:0}
html,body{width:1200px;height:5304px;overflow:hidden}
body{font-family:"Lato",sans-serif;color:var(--ink);background:var(--white);position:relative}
h1,h2,h3,h4{font-family:"Fira Sans",sans-serif;font-weight:500}
.abs{position:absolute}
.brand{display:flex;align-items:center;gap:10px;font-family:"Fira Sans",sans-serif;font-weight:600;font-size:26px;color:var(--orange)}
.brand .mark{width:30px;height:30px;border:3px solid var(--orange);border-radius:4px}
.btn{display:inline-flex;align-items:center;gap:10px;background:var(--orange);color:#fff;font-family:"Fira Sans",sans-serif;font-weight:500;font-size:15px;padding:10px 18px;border-radius:2px}
.eyebrow{font-size:10px;font-weight:700;letter-spacing:.5px;text-transform:uppercase}
.rule{width:84px;height:2px;background:var(--orange)}
.photo{position:absolute}
.topbar{top:0;left:0;width:1200px;height:46px;background:var(--topbar);color:#9fb3c0;font-size:10px}
.topbar span{position:absolute;top:17px}
.header{top:46px;left:0;width:1200px;height:129px}
.contact-item{position:absolute;top:38px;display:flex;gap:12px;font-size:11px;color:var(--ink)}
.contact-item small{display:block;color:var(--text);font-size:9px;margin-top:4px}
.nav{top:175px;left:78px;width:1044px;height:58px;background:var(--navy-2);display:flex;font-family:"Fira Sans",sans-serif;font-size:11px;font-weight:600;color:#fff}
.nav a{display:flex;align-items:center;justify-content:center;text-decoration:none;color:#fff}
.nav .active{background:var(--orange);width:78px}
.hero{top:233px;left:0;width:1200px;height:597px;background:linear-gradient(120deg,#1a2c55,#2c456f 45%,#16254a);text-align:center;color:#fff}
.hero h1{position:absolute;top:200px;width:100%;font-size:48px;font-weight:600;line-height:56px}
.hero p{position:absolute;top:325px;width:100%;font-size:14px;line-height:20px}
.hero .outline{position:absolute;top:395px;left:538px;width:132px;height:46px;border:2px solid #fff;font-family:"Fira Sans",sans-serif;font-size:12px;font-weight:600;display:flex;align-items:center;justify-content:center}
.why{top:830px;left:0;width:1200px;height:487px;background:linear-gradient(var(--light) 0 250px,#fff 250px)}
.center{text-align:center;width:100%;position:absolute}
.card{position:absolute;top:195px;width:341px;height:241px;background:#fff;box-shadow:0 4px 14px rgba(0,0,0,.08);text-align:center}
.card .num{position:absolute;top:0;right:0;width:58px;height:58px;border-bottom-left-radius:58px;background:var(--light);font-family:"Fira Sans",sans-serif;font-size:16px;color:#555;padding:22px 0 0 16px}
.card .icon{margin:42px auto 0;width:76px;height:76px;border-radius:50%;background:var(--light);display:flex;align-items:center;justify-content:center}
.card h4{margin-top:22px;font-size:16px}
.card .more{margin-top:12px;font-size:10px;font-weight:700;color:var(--orange)}
.about{top:1317px;left:0;width:1200px;height:630px}
.about p{font-size:14px;line-height:23px;color:var(--text)}
.tabs{top:1947px;left:64px;width:1072px;height:105px;background:#fff;border-top:5px solid var(--navy);display:flex;box-shadow:0 4px 10px rgba(0,0,0,.06);z-index:2}
.tabs div{flex:1;display:flex;align-items:center;justify-content:center;font-family:"Fira Sans",sans-serif;font-size:15px;font-weight:500;border-right:1px solid var(--line)}
.tabs .on{background:var(--orange);color:#fff}
.dark{top:2000px;left:0;width:1200px;height:610px;background:linear-gradient(90deg,#132248,#1b2f5c);color:#fff}
.gallery{top:2610px;left:0;width:1200px;height:744px}
.steps{top:3354px;left:0;width:1200px;height:646px}
.step-box{position:absolute;left:550px;width:100px;height:100px;background:#fff;box-shadow:0 4px 14px rgba(0,0,0,.1);display:flex;align-items:center;justify-content:center}
.step-box .badge{position:absolute;top:-14px;left:14px;width:28px;height:28px;border-radius:50%;background:var(--orange);color:#fff;font-size:12px;display:flex;align-items:center;justify-content:center;font-weight:700}
.step-text{position:absolute;left:700px;width:400px}
.step-text h4{font-size:16px;color:var(--navy);line-height:22px}
.step-text p{margin-top:20px;font-size:12.5px;line-height:22px;color:var(--text)}
.contact{top:4000px;left:0;width:1200px;height:723px}
.form{position:absolute;top:113px;left:590px;width:490px;height:548px;background:#fff;border-top:4px solid var(--navy);box-shadow:0 4px 20px rgba(0,0,0,.1)}
.form label{position:absolute;font-size:13px;font-weight:700;color:var(--navy)}
.form .field{position:absolute;border:1px solid var(--line);font-size:11px;color:#aaa;padding:14px 16px}
.info{position:absolute;left:140px;display:flex;gap:24px;align-items:center;font-size:13px;color:var(--text)}
.info .dot{width:30px;height:30px;border-radius:50%;background:#fde9da;display:flex;align-items:center;justify-content:center}
.footer{top:4723px;left:0;width:1200px;height:525px;background:var(--navy);color:#fff}
.footer h3{font-size:22px;font-weight:500}
.links{position:absolute;top:165px;font-size:14px;line-height:30px}
.links li{list-style:none}
.links li::before{content:"›";margin-right:14px}
.strip{position:absolute;top:432px;left:85px;width:1028px;height:88px;background:#24355a;display:flex}
.strip div{flex:1;display:flex;gap:22px;align-items:center;padding-left:30px;font-size:15px}
.strip b{display:block;font-size:14px}
.bottom{top:5248px;left:0;width:1200px;height:56px;font-size:12px;color:var(--text)}
</style>
</head>
<body>

<div class="abs topbar">
  <span style="left:78px">☎ &nbsp;+852 3018 4470</span>
  <span style="left:240px">hello@lumorasys.example</span>
  <span style="left:1020px">Search Information</span>
</div>

<header class="abs header">
  <div class="abs brand" style="left:97px;top:38px"><span class="mark"></span>Lumora Systems</div>
  <div class="contact-item" style="left:490px">
    <svg width="32" height="26" viewBox="0 0 40 30"><rect x="2" y="2" width="36" height="26" fill="none" stroke="#f7740f" stroke-width="2.5"/><path d="M2 2l18 14 18-14" fill="none" stroke="#f7740f" stroke-width="2.5"/></svg>
    <div>Email<small>info@lumorasys.example</small></div>
  </div>
  <div class="contact-item" style="left:750px">
    <svg width="30" height="30" viewBox="0 0 24 24"><path d="M5 3l4 1 1 5-2 2a12 12 0 0 0 5 5l2-2 5 1 1 4-3 2C10 21 3 14 2 6z" fill="none" stroke="#f7740f" stroke-width="1.6"/></svg>
    <div>Telephone<small>(852) 3018-4471</small></div>
  </div>
  <div class="contact-item" style="left:938px">
    <svg width="26" height="30" viewBox="0 0 24 28"><path d="M12 26s-9-9-9-15a9 9 0 0 1 18 0c0 6-9 15-9 15z" fill="none" stroke="#f7740f" stroke-width="1.8"/><circle cx="12" cy="11" r="3" fill="none" stroke="#f7740f" stroke-width="1.8"/></svg>
    <div>Location<small>18 Harbour Row, Kowloon</small></div>
  </div>
</header>

<nav class="abs nav">
  <a class="active">HOME</a>
  <a style="width:192px">ABOUT US</a>
  <a style="width:140px">SERVICES</a>
  <a style="width:180px">OUR TEAM</a>
  <a style="width:130px">PROJECTS</a>
  <a style="width:230px">CONTACT US</a>
</nav>

<section class="abs hero" role="img" aria-label="Dark blue server corridor with glowing cable racks">
  <h1>Pioneering Tomorrow's<br>Digital Landscape</h1>
  <p>Lorem ipsum dolor sit amet, consectetur adipiscing elit<br>sed do eiusmod tempor incidid</p>
  <div class="outline">LEARN MORE</div>
</section>

<section class="abs why">
  <div class="center eyebrow" style="top:62px;color:var(--text)">Why choose us</div>
  <h2 class="center" style="top:88px;font-size:36px;color:var(--navy)">Why we are the best</h2>
  <div class="rule abs" style="top:148px;left:558px"></div>
  <div class="card" style="left:64px"><div class="num">01</div><div class="icon"><svg width="34" height="34" viewBox="0 0 24 24"><circle cx="12" cy="12" r="8" fill="none" stroke="#f7740f" stroke-width="1.6"/><circle cx="12" cy="12" r="3" fill="none" stroke="#f7740f" stroke-width="1.6"/></svg></div><h4>Expertise</h4><div class="more">READ MORE</div></div>
  <div class="card" style="left:432px"><div class="num">02</div><div class="icon"><svg width="34" height="34" viewBox="0 0 24 24"><circle cx="8" cy="8" r="3" fill="none" stroke="#f7740f" stroke-width="1.6"/><circle cx="16" cy="8" r="3" fill="none" stroke="#f7740f" stroke-width="1.6"/><path d="M3 19c0-4 3-6 5-6s5 2 5 6M11 19c0-4 3-6 5-6s5 2 5 6" fill="none" stroke="#f7740f" stroke-width="1.6"/></svg></div><h4>Experience</h4><div class="more">READ MORE</div></div>
  <div class="card" style="left:798px"><div class="num">03</div><div class="icon"><svg width="34" height="34" viewBox="0 0 24 24"><path d="M4 16a8 8 0 1 1 16 0" fill="none" stroke="#f7740f" stroke-width="1.6"/><path d="M12 16l3-5" stroke="#f7740f" stroke-width="1.6"/></svg></div><h4>Professionalism</h4><div class="more">READ MORE</div></div>
</section>

<section class="abs about">
  <div class="abs eyebrow" style="left:92px;top:75px;color:var(--text);text-transform:none">About Us</div>
  <h2 class="abs" style="left:92px;top:98px;font-size:36px;color:var(--navy)">Sculpting Digital Landscapes</h2>
  <div class="rule abs" style="left:92px;top:158px"></div>
  <h3 class="abs" style="left:92px;top:190px;font-size:19px;color:var(--navy)">Empowering Growth through Data Excellence</h3>
  <p class="abs" style="left:92px;top:232px;width:505px">Lorem ipsum dolor sit amet, consectetur adipiscing elit, sed do eiusmod tempor incididunt ut labore et dolore magna aliqua. Ut enim ad minim veniam, quis nostrud exercitation ullamco laboris nisi ut aliquip ex ea commodo consequat. Duis aute irure dolor in reprehenderit in voluptate velit esse cillum dolore eu fugiat nulla pariatur. Excepteur sint occaecat cupidatat non proident, sunt in culpa qui officia deserunt mollit.</p>
  <svg class="abs" style="left:96px;top:432px" width="44" height="44" viewBox="0 0 24 24"><path d="M12 2l9 7-3 11H6L3 9z" fill="none" stroke="#f7740f" stroke-width="1.5"/></svg>
  <div class="abs" style="left:168px;top:432px;font-size:16px;line-height:25px;color:var(--navy)">Proven<br>Track Record</div>
  <svg class="abs" style="left:372px;top:432px" width="44" height="44" viewBox="0 0 24 24"><circle cx="10" cy="7" r="4" fill="none" stroke="#f7740f" stroke-width="1.5"/><path d="M3 21c0-5 3-8 7-8s7 3 7 8zM15 14l5-5" fill="none" stroke="#f7740f" stroke-width="1.5"/></svg>
  <div class="abs" style="left:443px;top:432px;font-size:16px;line-height:25px;color:var(--navy)">Personalised<br>Approach</div>
  <div class="abs btn" style="left:92px;top:527px">Learn More →</div>
  <div class="abs" style="left:668px;top:71px;width:434px;height:434px;border-radius:50%;border:2px solid var(--navy)"></div>
  <div class="photo" role="img" aria-label="Engineer with a laptop in a server room" style="left:684px;top:87px;width:402px;height:402px;border-radius:50%;background:linear-gradient(135deg,#5b6e86,#1e2f4c)"></div>
  <div class="abs" role="img" aria-label="Brand emblem placeholder" style="left:920px;top:305px;width:192px;height:192px;border-radius:50%;background:#1f3d8a"></div>
</section>

<section class="abs dark">
  <div class="photo" role="img" aria-label="Technician on a phone call beside server racks" style="left:64px;top:160px;width:522px;height:333px;background:linear-gradient(120deg,#2b3d5f,#6b7d96 55%,#233556)"></div>
  <div class="abs eyebrow" style="left:618px;top:127px;color:var(--orange)">About Us</div>
  <h2 class="abs" style="left:616px;top:150px;font-size:36px">Your Data, Our Commitment</h2>
  <div class="rule abs" style="left:618px;top:214px"></div>
  <h3 class="abs" style="left:616px;top:245px;font-size:20px;font-weight:400">Seamless Integration, Infinite Possibilities</h3>
  <p class="abs" style="left:618px;top:296px;width:505px;font-size:14px;line-height:23px">Lorem ipsum dolor sit amet, consectetur adipiscing elit, sed do eiusmod tempor incididunt ut labore et dolore magna aliqua. Ut enim ad minim veniam, quis nostrud exercitation ullamco laboris nisi ut aliquip ex ea commodo consequat. Duis aute irure dolor in reprehenderit in voluptate velit esse cillum dolore eu fugiat nulla pariatur. Excepteur sint occaecat cupidatat non proident, sunt in culpa qui officia deserunt mollit, proident, sunt in culpa qui officia deserunt mollit.</p>
  <div class="abs btn" style="left:620px;top:492px">Learn More →</div>
</section>
<div class="abs tabs"><div class="on">Data Centre Building</div><div>Structured Cabling</div><div style="border:none">Audio-Visual for Conferences</div></div>

<section class="abs gallery">
  <div class="center eyebrow" style="top:53px;color:var(--text)">Our Gallery</div>
  <h2 class="center" style="top:80px;font-size:36px;color:var(--navy)">Our Recent Work</h2>
  <div class="rule abs" style="top:140px;left:558px"></div>
  <div class="photo" role="img" aria-label="Close-up of blue lit server hardware" style="left:95px;top:179px;width:234px;height:232px;background:linear-gradient(135deg,#2751b0,#9aa9e0)"></div>
  <div class="photo" role="img" aria-label="Technician kneeling at a cable rack" style="left:354px;top:179px;width:233px;height:232px;background:linear-gradient(135deg,#56606b,#1f2a2e)"></div>
  <div class="photo" role="img" aria-label="Row of dark server cabinets" style="left:613px;top:179px;width:492px;height:232px;background:linear-gradient(90deg,#0d2b52,#1f4f82,#0e2a50)"></div>
  <div class="photo" role="img" aria-label="Hands typing on a laptop" style="left:95px;top:436px;width:492px;height:230px;background:linear-gradient(120deg,#1a2d4a,#6d85a8)"></div>
  <div class="photo" role="img" aria-label="Bright data centre aisle" style="left:613px;top:436px;width:233px;height:230px;background:linear-gradient(90deg,#1b2b45,#cfd8e3,#1b2b45)"></div>
  <div class="photo" role="img" aria-label="Server room with cyan lighting" style="left:871px;top:436px;width:234px;height:230px;background:linear-gradient(180deg,#38a7c9,#19265a)"></div>
</section>

<section class="abs steps">
  <div class="abs" role="img" aria-label="Dark blue server room backdrop" style="left:0;top:0;width:601px;height:646px;background:linear-gradient(135deg,#1a2d5c,#13234a)"></div>
  <div class="abs" style="left:601px;top:0;width:599px;height:646px;background:var(--light)"></div>
  <div class="abs eyebrow" style="left:99px;top:98px;color:#fff">How we work</div>
  <h2 class="abs" style="left:98px;top:120px;font-size:32px;color:#fff">Steps Involved</h2>
  <div class="rule abs" style="left:99px;top:177px"></div>
  <h3 class="abs" style="left:98px;top:218px;font-size:20px;color:#fff">Efficiency Redefined, Data Perfected</h3>
  <p class="abs" style="left:100px;top:265px;width:370px;font-size:13px;line-height:19px;color:#fff">Lorem ipsum dolor sit amet, consectetur adipiscing d tempor incididunt ut labore et dolore magna al m veniam, quis nostrud exercitation ullamco laboris commodo consequat. Duis aute irure dolor in repr tate velit esse cillum dolore eu fugiat nulla pariat aecat cupidatat</p>
  <div class="abs btn" style="left:100px;top:480px">Contact us →</div>

  <div class="step-box" style="top:106px"><span class="badge">01</span><svg width="40" height="30" viewBox="0 0 40 30"><rect x="2" y="2" width="36" height="26" fill="none" stroke="#f7740f" stroke-width="2.5"/><path d="M2 2l18 14 18-14" fill="none" stroke="#f7740f" stroke-width="2.5"/></svg></div>
  <div class="step-text" style="top:106px"><h4>Get in touch<br>with us</h4><p>Lorem ipsum dolor sit amet, consectetur adipiscing d te mpor incididunt ut labore et dolore magna alm veniam</p></div>
  <div class="step-box" style="top:275px"><span class="badge">02</span><svg width="44" height="44" viewBox="0 0 24 24"><rect x="3" y="3" width="7" height="6" fill="none" stroke="#f7740f" stroke-width="1.6"/><rect x="14" y="3" width="7" height="6" fill="none" stroke="#f7740f" stroke-width="1.6"/><circle cx="12" cy="15" r="3" fill="#f7740f"/><path d="M7 22c0-3 2-4 5-4s5 1 5 4" fill="#f7740f"/></svg></div>
  <div class="step-text" style="top:275px"><h4>Get an assessment<br>from our experts</h4><p>Lorem ipsum dolor sit amet, consectetur adipiscing d te mpor incididunt ut labore et dolore magna alm veniam</p></div>
  <div class="step-box" style="top:444px"><span class="badge">03</span><svg width="42" height="42" viewBox="0 0 24 24"><circle cx="8" cy="8" r="3" fill="none" stroke="#f7740f" stroke-width="1.6"/><circle cx="16" cy="8" r="3" fill="none" stroke="#f7740f" stroke-width="1.6"/><path d="M3 19c0-4 3-6 5-6s5 2 5 6M11 19c0-4 3-6 5-6s5 2 5 6" fill="none" stroke="#f7740f" stroke-width="1.6"/></svg></div>
  <div class="step-text" style="top:444px"><h4>Enjoy Seamless<br>Data Connection</h4><p>Lorem ipsum dolor sit amet, consectetur adipiscing d te mpor incididunt ut labore et dolore magna alm veniam</p></div>
</section>

<section class="abs contact">
  <h2 class="abs" style="left:138px;top:178px;font-size:35px;font-weight:600;line-height:46px;color:var(--navy)">Get in touch<br>with us</h2>
  <p class="abs" style="left:140px;top:292px;width:370px;font-size:12.5px;line-height:22px;color:var(--text)">Lorem ipsum dolor sit amet, consectetur adipiscing elit, sed do eiusmod tempor incididunt ut labore et dolore magna aliqua. Ut enim</p>
  <div class="abs" style="left:140px;top:390px;width:380px;height:1px;background:var(--line)"></div>
  <div class="info" style="top:425px"><span class="dot"><svg width="14" height="16" viewBox="0 0 24 28"><path d="M12 26s-9-9-9-15a9 9 0 0 1 18 0c0 6-9 15-9 15z" fill="#f7740f"/></svg></span>18 Harbour Row</div>
  <div class="info" style="top:480px"><span class="dot"><svg width="14" height="14" viewBox="0 0 24 24"><path d="M5 3l4 1 1 5-2 2a12 12 0 0 0 5 5l2-2 5 1 1 4-3 2C10 21 3 14 2 6z" fill="#f7740f"/></svg></span>+852 3018 4472</div>
  <div class="info" style="top:535px"><span class="dot"><svg width="14" height="12" viewBox="0 0 40 30"><rect x="2" y="2" width="36" height="26" fill="#f7740f"/></svg></span>office@lumorasys.example</div>
  <div class="form">
    <label style="left:36px;top:50px">Full Name:</label>
    <div class="field" style="left:30px;top:80px;width:428px;height:44px">Sed non neque elit</div>
    <label style="left:36px;top:158px">Email:</label>
    <label style="left:262px;top:158px">Phone-no:</label>
    <div class="field" style="left:30px;top:190px;width:198px;height:44px">Sed non neque elit</div>
    <div class="field" style="left:258px;top:190px;width:200px;height:44px">Sed non neque elit</div>
    <label style="left:36px;top:270px">Messages:</label>
    <div class="field" style="left:30px;top:300px;width:428px;height:128px">Sed non neque elit</div>
    <div class="btn" style="position:absolute;left:30px;top:462px;font-size:12px;padding:12px 38px">SUBMIT</div>
  </div>
</section>

<footer class="abs footer">
  <div class="abs brand" style="left:97px;top:95px"><span class="mark"></span>Lumora Systems</div>
  <div class="abs" style="left:84px;top:168px;font-size:18px;font-weight:700">852-3018-4473</div>
  <div class="abs" style="left:84px;top:193px;font-size:13px;font-weight:700">Call for free consultation</div>
  <p class="abs" style="left:84px;top:230px;width:290px;font-size:13px;line-height:21px">Lorem ipsum dolor sit amet, consectet sed do eiusmod tempor incididunt ut la magna aliqua. Ut enim</p>
  <div class="abs" style="left:84px;top:315px;font-size:14px;font-weight:700">Read more ›</div>
  <h3 class="abs" style="left:438px;top:95px">Useful Links</h3>
  <ul class="links" style="left:443px"><li>About Company</li><li>Leadership</li><li>Blog Post</li><li>FAQ'S</li><li>Certification</li><li>Testimonials</li></ul>
  <ul class="links" style="left:606px"><li>Services</li><li>Industries</li><li>Feedback</li><li>Partners</li><li>Pricing</li><li>Contct</li></ul>
  <h3 class="abs" style="left:789px;top:95px">Newsletter</h3>
  <p class="abs" style="left:788px;top:177px;width:330px;font-size:12px;line-height:24px">Dont miss to subscribe to our news feeds, kindly fill the form below</p>
  <div class="abs" style="left:788px;top:255px;width:320px;height:48px;border-radius:24px;background:var(--navy);border:1px solid #2a3d66;font-size:12px;padding:17px 24px">Your Email Address</div>
  <div class="abs" style="left:1056px;top:255px;width:52px;height:48px;border-radius:0 24px 24px 0;background:var(--orange);display:flex;align-items:center;justify-content:center;font-size:22px">›</div>
  <div class="strip">
    <div><svg width="30" height="34" viewBox="0 0 24 28"><path d="M12 26s-9-9-9-15a9 9 0 0 1 18 0c0 6-9 15-9 15z" fill="none" stroke="#f7740f" stroke-width="1.8"/><circle cx="12" cy="11" r="3" fill="none" stroke="#f7740f" stroke-width="1.8"/></svg><span><b>Location</b>18 Harbour Row, Kowloon</span></div>
    <div><svg width="32" height="28" viewBox="0 0 32 28"><rect x="2" y="2" width="28" height="20" fill="none" stroke="#f7740f" stroke-width="2"/><path d="M8 9h16M8 15h12" stroke="#f7740f" stroke-width="2"/></svg><span><b>Mail us</b>support@lumorasys.example</span></div>
    <div><svg width="30" height="30" viewBox="0 0 24 24"><path d="M2 11L22 3l-7 19-4-8z" fill="none" stroke="#f7740f" stroke-width="1.8"/></svg><span><b>Office hrs</b>9.00am to 7.00pm (Mon-Sat)</span></div>
  </div>
  <div class="abs" style="left:1124px;top:475px;width:46px;height:46px;background:var(--orange);display:flex;align-items:center;justify-content:center;font-size:20px">⌃</div>
</footer>

<div class="abs bottom">
  <span class="abs" style="left:85px;top:26px">Lumora Systems</span>
  <span class="abs" style="left:801px;top:26px">Privacy Policy</span>
  <span class="abs" style="left:911px;top:26px">Terms &amp; Conditions</span>
  <span class="abs" style="left:1054px;top:26px">Site Map</span>
</div>

</body>
</html>
```